Stationery Design Project

Hi All,

We need you to design stationary for a new Business and Accounting Advisory Firm. We have already got the logo designed and it is attached. If you could also if possible, match the fonts in your design to that on the logo’s provided.

What we need:
- Business Card
- A4 Letter head
- A4 Folders
- PPT template (Title page and regular page)

And what ever else you want to throw in.

We are in the process of getting the web site designed, however below is a list of websites which we like which will give you an understanding of the style that we are going for.

- plivant.example
- moldrabay.example
- tarvenhook.example
- quillorbank.example

I look forward to your seeing your design.
Updates

Hi All,

I have just realised that I forgot that i need to include a Sworn Ledgerkeepers image on the letter head, please find attaced as File 1. Could you please have this image in the bottom left header.

Regards,

Marcus

Industry/Entity Type

Business

Requirements
Must have
• Outputs:
- Documents ready to print
- Generic editable information
- Pdf copies of the documents
- Word version of letterhead

```html
<!DOCTYPE html>
<html lang="en">
<head>
<meta charset="utf-8">
<title>Dunmore Partners – Business Cards</title>
<link href="https://fonts.googleapis.com/css2?family=EB+Garamond:wght@400;500&family=Tinos:wght@400;700&display=swap" rel="stylesheet">
<style>
  :root {
    --backdrop: #898c8e;
    --paper: #ffffff;
    --brand-blue: #3b5b9c;
    --brand-cyan: #40c2dd;
    --brand-orange: #f7941d;
    --ink: #2a2a2a;
    --rule-grey: #c9c9c9;
  }
  * { margin: 0; padding: 0; box-sizing: border-box; }
  html, body { width: 1200px; height: 709px; overflow: hidden; }
  body { background: var(--backdrop); position: relative; font-family: "Tinos", "Times New Roman", serif; }

  .card { position: absolute; background: var(--paper); overflow: hidden; }
  .card--front { left: 319px; top: 18px; width: 558px; height: 320px; }
  .card--plain { left: 33px; top: 363px; width: 557px; height: 318px; border: 1px solid #6d6f71; }
  .card--back {
    left: 614px; top: 363px; width: 558px; height: 318px;
    background: radial-gradient(circle at 52% 50%, var(--brand-cyan) 0%, #3a85bb 28%, var(--brand-blue) 62%);
  }

  .brand { position: absolute; display: flex; align-items: center; gap: 14px; }
  .brand__square { width: 22px; height: 22px; background: var(--brand-orange); }
  .brand__name {
    font-family: "EB Garamond", Georgia, serif; font-weight: 500;
    color: var(--brand-blue); white-space: nowrap; line-height: 1;
  }
  .card--front .brand { left: 106px; top: 78px; }
  .card--front .brand__name { font-size: 36px; }
  .card--plain .brand { left: 84px; top: 128px; }
  .card--plain .brand__name { font-size: 40px; }

  .holder { position: absolute; right: 313px; top: 176px; text-align: right; color: var(--ink); }
  .holder__name { font-weight: 700; font-size: 21px; color: var(--brand-blue); line-height: 26px; }
  .holder__role { font-size: 16px; line-height: 20px; }
  .holder__address { font-size: 16px; line-height: 22px; margin-top: 10px; }

  .divider { position: absolute; left: 259px; top: 172px; width: 1px; height: 107px; background: var(--rule-grey); }

  .contacts { position: absolute; left: 270px; top: 182px; list-style: none; color: #1f1f1f; }
  .contacts li { display: flex; align-items: center; gap: 6px; font-size: 17px; line-height: 23px; }
  .contacts svg { width: 11px; height: 11px; fill: var(--brand-blue); flex: none; }

  .stripe-orange { position: absolute; left: 0; top: 291px; width: 100%; height: 2px; background: var(--brand-orange); }
  .stripe-band {
    position: absolute; left: 0; top: 295px; width: 100%; height: 25px;
    background: linear-gradient(90deg, var(--brand-blue) 0%, #3a6fb0 45%, var(--brand-cyan) 100%);
  }

  .web { position: absolute; left: 0; width: 100%; text-align: center; letter-spacing: 1.6px; }
  .card--plain .web { top: 240px; font-size: 18px; color: #111; }
  .card--back .web { top: 265px; font-size: 17px; color: var(--paper); }

  .back-name {
    position: absolute; left: 0; top: 110px; width: 100%; text-align: center;
    font-family: "EB Garamond", Georgia, serif; font-weight: 500;
    font-size: 54px; color: var(--paper); line-height: 1;
  }
</style>
</head>
<body>

<section class="card card--front">
  <div class="brand">
    <span class="brand__square"></span>
    <span class="brand__name">Dunmore Partners</span>
  </div>

  <div class="holder">
    <p class="holder__name">Your Name</p>
    <p class="holder__role">Designation</p>
    <p class="holder__address">Street Name, City Name<br>State, City Zip Code</p>
  </div>

  <div class="divider"></div>

  <ul class="contacts">
    <li><svg viewBox="0 0 12 12"><path d="M3 1l2 2.5-1.2 1.3c.7 1.5 1.9 2.7 3.4 3.4L8.5 7 11 9l-1.2 2C5.5 11 1 6.5 1 2.2z"/></svg>0123-456-789</li>
    <li><svg viewBox="0 0 12 12"><rect x="3" y="0.5" width="6" height="11" rx="1.2"/><rect x="4" y="2" width="4" height="6.5" fill="#fff"/></svg>0123-456-789</li>
    <li><svg viewBox="0 0 12 12"><rect x="0.5" y="2.5" width="11" height="7.5" rx="1"/><path d="M1 3l5 4 5-4" stroke="#fff" stroke-width="1.1" fill="none"/></svg>info@dunmorepartners.example</li>
    <li><svg viewBox="0 0 12 12"><circle cx="6" cy="6" r="5.2"/><path d="M1 6h10M6 1c-2.5 3-2.5 7 0 10M6 1c2.5 3 2.5 7 0 10" stroke="#fff" stroke-width="0.8" fill="none"/></svg>www.dunmorepartners.example</li>
  </ul>

  <div class="stripe-orange"></div>
  <div class="stripe-band"></div>
</section>

<section class="card card--plain">
  <div class="brand">
    <span class="brand__square"></span>
    <span class="brand__name">Dunmore Partners</span>
  </div>
  <p class="web">www.dunmorepartners.example</p>
</section>

<section class="card card--back">
  <p class="back-name">Dunmore Partners</p>
  <p class="web">www.dunmorepartners.example</p>
</section>

</body>
</html>
```